Business Card for Coastal Tundrabridge Advisory

We need a business card for Coastal Tundrabridge Advisory. The company website address is provided below. The company logo is attached. We provide specialized permafrost services to the mining, transportation, and oil & gas industries. The card should be prepared for:
Matthias Korhonen, PhD.
Coastal Tundrabridge Advisory
PO Box 418259
Quillwater, Alaska 99642
Direct: +1-907-555-0143
Email: mkorhonen@tundrabridgeadvisory.example
Website: www.coastaltundrabridgeadvisory.example

```html
<!DOCTYPE html>
<html lang="en">
<head>
<meta charset="utf-8">
<title>Coastal Tundrabridge Advisory – Business Card</title>
<link href="https://fonts.googleapis.com/css2?family=Open+Sans:ital,wght@1,700&family=Roboto+Condensed:wght@700&display=swap" rel="stylesheet">
<style>
  :root {
    --backdrop: #efefef;
    --card-light: #ffffff;
    --card-dark: #2f2f2f;
    --ink: #2b2b2b;
    --frame: #7a7a7a;
    --rule: #8a8a8a;
    --gold: #a39245;
  }
  * { box-sizing: border-box; margin: 0; padding: 0; }
  html, body {
    width: 1200px; height: 1199px; overflow: hidden;
    background: var(--backdrop);
  }
  .sheet { position: relative; width: 1200px; height: 1199px; }

  .card {
    position: absolute; left: 237px; width: 726px; height: 412px;
    border-radius: 28px;
  }
  .card--front { top: 156px; background: var(--card-light); }
  .card--back  { top: 648px; background: var(--card-dark); }

  .card__frame { position: absolute; inset: 0; }

  .identity {
    position: absolute; right: 385px; top: 166px; text-align: right;
    font-family: "Open Sans", sans-serif; font-style: italic; font-weight: 700;
    color: var(--ink);
  }
  .identity__name { font-size: 22px; letter-spacing: -0.5px; line-height: 1.2; }
  .identity__role { font-size: 9px; margin-top: 6px; }

  .divider {
    position: absolute; left: 361px; top: 124px; width: 1.5px; height: 132px;
    background: var(--rule);
  }

  .contacts {
    position: absolute; left: 380px; top: 144px; list-style: none;
    font-family: "Roboto Condensed", sans-serif; font-weight: 700;
    font-size: 13.5px; color: var(--ink);
  }
  .contacts li { display: flex; align-items: center; height: 27px; }
  .contacts svg { width: 19px; height: 19px; margin-right: 8px; flex: none; }

  .address {
    position: absolute; left: 0; right: 0; top: 350px; text-align: center;
    font-family: "Roboto Condensed", sans-serif; font-weight: 700;
    font-size: 13px; line-height: 19px; color: var(--ink);
  }

  .brand-name {
    position: absolute; left: 0; right: 0; top: 182px; text-align: center;
    font-family: "Roboto Condensed", sans-serif; font-weight: 700;
    font-size: 33px; letter-spacing: 4px; text-transform: uppercase;
    color: var(--gold);
  }
</style>
</head>
<body>
<main class="sheet">

  <section class="card card--front" aria-label="Card front">
    <svg class="card__frame" viewBox="0 0 726 412" aria-hidden="true">
      <path d="M149 372 H45 Q21 372 21 348 V41 Q21 17 45 17 H681 Q705 17 705 41 V348 Q705 372 681 372 H575"
            fill="none" stroke="var(--frame)" stroke-width="2.5"/>
    </svg>

    <div class="identity">
      <p class="identity__name">Matthias Korhonen, PhD</p>
      <p class="identity__role">Founder &amp; Director</p>
    </div>

    <div class="divider"></div>

    <ul class="contacts">
      <li>
        <svg viewBox="0 0 20 20" aria-hidden="true"><circle cx="10" cy="10" r="8.5" fill="none" stroke="#555" stroke-width="1.2"/><path d="M7 6 l1.5 -0.5 1 2 -1 1 q1 2 2.5 2.5 l1 -1 2 1 -0.5 1.5 q-4 0.5 -6.5 -6.5z" fill="#555"/></svg>
        +1-907-555-0143
      </li>
      <li>
        <svg viewBox="0 0 20 20" aria-hidden="true"><circle cx="10" cy="10" r="8.5" fill="none" stroke="#555" stroke-width="1.2"/><rect x="7" y="5" width="6" height="10" rx="1" fill="none" stroke="#555" stroke-width="1.2"/></svg>
        (907) 555 0178
      </li>
      <li>
        <svg viewBox="0 0 20 20" aria-hidden="true"><circle cx="10" cy="10" r="8.5" fill="none" stroke="#555" stroke-width="1.2"/><rect x="5.5" y="7" width="9" height="6.5" fill="#555"/><path d="M5.5 7 L10 10.5 L14.5 7" fill="none" stroke="#fff" stroke-width="1"/></svg>
        mkorhonen@tundrabridgeadvisory.example
      </li>
      <li>
        <svg viewBox="0 0 20 20" aria-hidden="true"><circle cx="10" cy="10" r="8.5" fill="none" stroke="#555" stroke-width="1.2"/><circle cx="10" cy="10" r="5" fill="none" stroke="#555" stroke-width="1"/><ellipse cx="10" cy="10" rx="2" ry="5" fill="none" stroke="#555" stroke-width="1"/><path d="M5 10 H15" stroke="#555" stroke-width="1"/></svg>
        www.coastaltundrabridgeadvisory.example
      </li>
    </ul>

    <address class="address" style="font-style:normal">
      PO Box 418259<br>
      Quillwater, Alaska 99642
    </address>
  </section>

  <section class="card card--back" aria-label="Card back">
    <p class="brand-name">Coastal Tundrabridge Advisory</p>
  </section>

</main>
</body>
</html>
```